Modern claims management company

We need a new company presentation brochure, composed of about 20 pages in A4 format.
Cover, page 1 who we are, page 2 company profile, page 3 territorial operation, page from 4 to 10 services offered and description of services (The title of the page are: Perizie e Liquidazione danni, riparazioni e sostituzioni, teleclaimer, accertamento danni da fenomeno elettrico, TPA, Auditing, drone pilot, Valutazione rischi), from 11 to 17 specializations (Sinistri gravi, R.C., Tecnologici, Energie rinnovabili, strutture, ambiente) page 18 e 19 integrated services (perdite occulte, ricerca guasti, indagini termografiche, crisis management), page 20 clients ( list companies and logos) page 21 contact.
The company is made up of various companies, which belong to the principal, each of which deals with specific activities.
To date we already have various logos of the main company (Varesco and Tundi) as well as the logos of the other companies. I load them on the portal.
Found then the graphic solution that we like we will have to proceed to make a presentation in similar powerpoint and the website.

Target Market(s)

Insurance Company, Insurance Broker

Font styles to use
Other font styles liked:
• ARIAL

Colors
333333
5c5c5c
959595
0392cd

Requirements
Must have
• It must be clear, professional and modern.
Nice to have
• I indicate some competitor sites, so that you can better understand what we are doing. www.brantows.com, www.pemberwellhastons.com, www.ortevisandri.com, www.gruppotavesi.com, www.varduzzo.eu.

```html
<!DOCTYPE html>
<html lang="en">
<head>
<meta charset="utf-8">
<title>Varesco and Tundi – Services Brochure Spread</title>
<link rel="stylesheet" href="https://fonts.googleapis.com/css2?family=Arimo:ital,wght@0,400;0,700;1,400;1,700&family=Open+Sans:wght@400;600&display=swap">
<style>
  :root{
    --ink:#333333;
    --grey:#5c5c5c;
    --mid:#959595;
    --blue:#0392cd;
    --navy:#0d5ea8;
    --deep:#0a4f96;
    --paper:#f2f4f6;
    --stage:#e6e7e9;
    --white:#ffffff;
  }
  html,body{margin:0;padding:0;overflow:hidden;}
  body{width:1200px;height:1200px;background:var(--stage);position:relative;font-family:"Arimo",Arial,sans-serif;}
  .spread{position:absolute;left:30px;top:197px;width:1140px;height:806px;overflow:hidden;box-shadow:0 6px 22px rgba(0,0,0,.18);}
  .spread-art{position:absolute;inset:0;}
  .fold{position:absolute;top:0;bottom:0;width:1px;background:rgba(0,0,0,.12);}
  .t{position:absolute;margin:0;}
  .heading-news{font-family:"Open Sans",sans-serif;font-size:22px;font-weight:400;color:var(--ink);line-height:26px;}
  .lead-small{font-size:10px;line-height:13px;color:var(--grey);}
  .body-dark{font-size:11px;line-height:14px;color:var(--ink);}
  .section-white{font-size:22px;font-weight:700;color:var(--white);line-height:26px;}
  .body-white{font-size:11px;line-height:15px;color:var(--white);}
  .list-white{font-size:11px;line-height:14px;font-weight:700;color:var(--white);list-style:none;padding:0;}
  .subhead-blue{font-size:17px;font-weight:700;font-style:italic;color:var(--blue);line-height:19px;}
  .italic-dark{font-size:10.5px;line-height:13px;font-style:italic;color:var(--ink);}
  .subhead-white-italic{font-size:19px;font-weight:700;font-style:italic;color:var(--white);line-height:22px;}
  .italic-white{font-size:10.5px;line-height:13px;font-style:italic;color:var(--white);text-align:justify;}
  .list-italic{font-size:10.5px;line-height:13px;font-style:italic;color:var(--white);list-style:none;padding:0;}
  .list-italic.bold{font-weight:700;}
  .heading-panel{font-size:18px;font-weight:700;color:var(--navy);line-height:22px;}
  .list-black{font-size:11px;line-height:13px;font-weight:700;color:#111;list-style:none;padding:0;}
  .heading-white{font-size:21px;font-weight:700;color:var(--white);line-height:24px;}
  .body-soft{font-size:11.5px;line-height:15px;color:rgba(255,255,255,.78);}
  .questions{font-size:11px;line-height:14px;font-weight:700;color:var(--white);}
  .rule{position:absolute;height:1px;background:rgba(255,255,255,.55);}
</style>
</head>
<body>
<main class="spread">
  <svg class="spread-art" width="1140" height="806" viewBox="0 0 1140 806">
    <defs>
      <linearGradient id="blueBody" x1="0" y1="0" x2="0" y2="1">
        <stop offset="0" stop-color="#4cb8e6"/>
        <stop offset="0.6" stop-color="#1d86cf"/>
        <stop offset="1" stop-color="#0a56a0"/>
      </linearGradient>
      <linearGradient id="rightBody" x1="0" y1="0" x2="0" y2="1">
        <stop offset="0" stop-color="#2f8fd6"/>
        <stop offset="1" stop-color="#1766b3"/>
      </linearGradient>
      <linearGradient id="photoTop" x1="0" y1="0" x2="1" y2="1">
        <stop offset="0" stop-color="#3a4f7a"/>
        <stop offset="0.5" stop-color="#8c8a86"/>
        <stop offset="1" stop-color="#5f6b78"/>
      </linearGradient>
      <linearGradient id="photoHouses" x1="0" y1="0" x2="1" y2="1">
        <stop offset="0" stop-color="#c9c03a"/><stop offset="1" stop-color="#6f7b4a"/>
      </linearGradient>
      <linearGradient id="photoWorker" x1="0" y1="0" x2="1" y2="1">
        <stop offset="0" stop-color="#e2652a"/><stop offset="1" stop-color="#8a8e96"/>
      </linearGradient>
      <linearGradient id="photoHelmets" x1="0" y1="0" x2="1" y2="1">
        <stop offset="0" stop-color="#2f3a3f"/><stop offset="1" stop-color="#3fae4d"/>
      </linearGradient>
      <linearGradient id="photoMetal" x1="0" y1="0" x2="1" y2="1">
        <stop offset="0" stop-color="#8a6e5c"/><stop offset="1" stop-color="#4d3e35"/>
      </linearGradient>
      <linearGradient id="photoCrowd" x1="0" y1="0" x2="1" y2="1">
        <stop offset="0" stop-color="#8e96a0"/><stop offset="1" stop-color="#49525c"/>
      </linearGradient>
    </defs>

    <rect class="field-blue" x="0" y="0" width="760" height="806" fill="url(#blueBody)"/>
    <rect class="field-right" x="760" y="0" width="380" height="806" fill="url(#rightBody)"/>
    <polygon class="field-light" points="0,0 760,0 760,230 690,330 560,345 470,420 360,430 0,395" fill="var(--paper)"/>
    <polygon class="band-bottom" points="0,610 760,630 760,806 0,806" fill="#0b5aa4" opacity=".55"/>
    <polygon class="band-bottom-mid" points="380,650 760,640 760,806 380,806" fill="#0a4f96" opacity=".5"/>
    <polygon class="field-right-light" points="760,0 1140,0 1140,250 1060,262 980,240 760,245" fill="var(--paper)"/>
    <polygon class="band-right-bottom" points="760,690 1140,690 1140,806 760,806" fill="var(--deep)" opacity=".5"/>

    <g role="img" aria-label="Photograph: site inspectors in hard hats and suits walking past a crane and construction machinery">
      <polygon points="0,0 760,0 760,60 700,150 520,150 470,110 0,110" fill="url(#photoTop)"/>
    </g>
    <g role="img" aria-label="Photograph: aerial view of suburban rooftops among trees">
      <polygon points="215,300 335,300 378,375 335,450 215,450 172,375" fill="url(#photoHouses)"/>
    </g>
    <g role="img" aria-label="Photograph: rescue worker in orange overalls on a disaster site">
      <polygon points="640,170 760,170 760,330 640,330 600,250" fill="url(#photoWorker)"/>
    </g>
    <g role="img" aria-label="Photograph: workers in green hard hats inspecting building services">
      <polygon points="440,375 545,375 585,440 545,505 440,505 400,440" fill="url(#photoHelmets)"/>
    </g>
    <g role="img" aria-label="Photograph: interlocking metal puzzle pieces">
      <polygon points="985,345 1100,345 1135,410 1100,478 985,478 950,410" fill="url(#photoMetal)"/>
    </g>
    <g role="img" aria-label="Photograph: crowd of people crossing a wide street seen from above">
      <polygon points="965,560 1105,560 1140,625 1105,690 965,690 930,625" fill="url(#photoCrowd)"/>
    </g>
  </svg>

  <div class="fold" style="left:380px"></div>
  <div class="fold" style="left:760px"></div>

  <!-- Panel 1 -->
  <h2 class="t heading-news" style="left:22px;top:150px;">What's happening at</h2>
  <p class="t lead-small" style="left:22px;top:182px;width:330px;">Every day we help our clients deal with complex, fascinating risks. Find out our latest news.</p>
  <h2 class="t heading-news" style="left:22px;top:214px;">Our services</h2>
  <p class="t body-dark" style="left:22px;top:248px;width:145px;">Whether you want high-volume claims management, complex loss adjusting, TPA, risk consultancy or repair and restoration - we can be relied upon to get the job done, using the right people, across the world.</p>

  <h2 class="t section-white" style="left:22px;top:462px;">General Loss Adjusting</h2>
  <p class="t body-white" style="left:22px;top:500px;width:335px;">Think of us as the fourth emergency service.<br>Our adjusters use their expertise to assess if policy wording is applicable to the loss, sums insured are at the right level, that the amount claimed is reasonable and if all valid items have been claimed. We offer you the following services:</p>
  <div class="rule" style="left:22px;top:608px;width:335px;"></div>
  <ul class="t list-white" style="left:22px;top:620px;">
    <li>Claims handling;</li>
    <li>Personal lines loss adjusting;</li>
    <li>Commercial loss adjusting;</li>
    <li>Major and complex loss;</li>
    <li>Claim management assistance</li>
  </ul>

  <!-- Panel 2 -->
  <h3 class="t subhead-blue" style="left:402px;top:190px;">Catastrophe<br>Response</h3>
  <p class="t italic-dark" style="left:402px;top:236px;width:185px;">Catastrophe events are the ultimate test of our industry.</p>
  <p class="t italic-dark" style="left:402px;top:268px;width:185px;">We have dealt with some of the biggest events on record - including the New Zealand earthquakes, Hurricane Katrina and London riots. You will be in safe hands.</p>

  <h3 class="t subhead-white-italic" style="left:595px;top:398px;">Building<br>Consulting<br>Services</h3>
  <p class="t italic-white" style="left:402px;top:528px;width:340px;">Our consultants assess each case on its individual merits, and have the experience to truly understand and deliver to your unique consulting needs.</p>
  <p class="t italic-white" style="left:402px;top:574px;width:340px;">From our offices in Australia, USA and New Zealand, Tundreth offers significant building cost management benefits, with support in the following areas:</p>
  <ul class="t list-italic" style="left:402px;top:672px;">
    <li>Causation reports;</li>
    <li>Estimate of damages;</li>
    <li>Quantity surveying reports;</li>
    <li>Major Loss project management;</li>
  </ul>
  <ul class="t list-italic bold" style="left:585px;top:680px;">
    <li>Home warranty identification</li>
    <li>Quantity Surveying</li>
    <li>Structural Engineering</li>
  </ul>

  <!-- Panel 3 -->
  <h2 class="t heading-panel" style="left:780px;top:54px;">Major &amp; Complex Loss Adjusting</h2>
  <p class="t body-dark" style="left:780px;top:82px;width:340px;">Our Major &amp; Complex Loss (MCV Global) team has the expertise and experience to give you world class advice and a cost-effective, fair claims handling service to get businesses up and running as quickly as possible.</p>
  <ul class="t list-black" style="left:780px;top:146px;">
    <li>Construction and Engineering</li>
    <li>Cyber and Technology</li>
    <li>Marine</li>
    <li>Mining</li>
    <li>Overview of Major &amp; Complex Loss</li>
    <li>Power</li>
    <li>Product Liability &amp; Recall</li>
  </ul>

  <h2 class="t heading-white" style="left:780px;top:278px;">Forensic Advisory<br>Services</h2>
  <p class="t body-soft" style="left:780px;top:336px;width:165px;">Orvant Global specialise in providing financial forensics and investigation services to the insurance industry, legal, corporate and public sectors globally</p>

  <h2 class="t heading-white" style="left:780px;top:476px;">Third Party<br>Administration</h2>
  <p class="t body-soft" style="left:780px;top:534px;width:145px;">Orvant Global specialise in providing financial forensics and investigation services to the insurance industry, legal, corporate and public sectors globally</p>

  <p class="t questions" style="left:780px;top:706px;width:345px;">Have too many or too few claims to manage effectively in-house<br>Are dealing with new or highly-complex claims<br>Need global TPA cover which complies with regulatory, legal and cultural requirements and covers all time-zones, languages and currencies<br>Need a consolidated view of their data</p>
</main>
</body>
</html>
```